Verdana Crest New Website - Online Learning and Education

New Wordpress website for an online learning site that has courses, worksheets, quizzes, etc.
Updates

We would like something similar to this website: https://hallowaybridgeinstitute.example/mediation-skills-course/. But continue with the content of our current website: http://verdanacrestlearninghub.example

We would like something similar to this site: https://hallowaybridgeinstitute.example/mediation-skills-course/

Coding

Coded - Design and coding required

```html
<!DOCTYPE html>
<html lang="en">
<head>
<meta charset="utf-8">
<title>Verdana Crest – Online Learning</title>
<link href="https://fonts.googleapis.com/css2?family=Montserrat:wght@400;500;600&family=Open+Sans:wght@400;600&display=swap" rel="stylesheet">
<style>
:root{
  --navy:#163a7a;
  --navy-dark:#15336b;
  --red:#b2142a;
  --ink:#222;
  --muted:#666;
  --band:#e5e5e5;
  --footer:#232323;
  --white:#fff;
}
*{box-sizing:border-box;margin:0;padding:0}
html,body{width:1200px;height:3332px;overflow:hidden;background:var(--white)}
body{position:relative;font-family:"Open Sans",sans-serif;color:var(--ink)}
.abs{position:absolute}
h1,h2,h3{font-family:"Montserrat",sans-serif;font-weight:500}

/* header */
.site-header{position:absolute;left:0;top:0;width:1200px;height:71px;background:var(--white)}
.brand{position:absolute;left:145px;top:20px;display:flex;align-items:center;gap:10px;font-family:"Montserrat",sans-serif;font-weight:600;font-size:24px;color:var(--navy)}
.brand-dot{width:30px;height:30px;border-radius:50%;background:var(--navy)}
.nav a{position:absolute;top:28px;font-family:"Montserrat",sans-serif;font-size:13px;color:#444;text-decoration:none}
.nav a.active{color:var(--navy)}
.btn{position:absolute;top:22px;height:31px;line-height:31px;text-align:center;font-family:"Montserrat",sans-serif;font-size:13px;color:var(--white);border-radius:2px}
.btn-login{left:903px;width:63px;background:var(--navy)}
.btn-register{left:975px;width:80px;background:var(--red)}

/* hero */
.hero{position:absolute;left:0;top:71px;width:1200px;height:543px;background:linear-gradient(100deg,#8e8f91 0%,#5b6472 30%,#3a4b66 45%,#c9c5bd 70%,#8c7a63 100%)}
.hero-arrow{position:absolute;top:258px}
.search-panel{position:absolute;left:720px;top:164px;width:335px;height:215px;background:linear-gradient(110deg,#1c3c7c 0%,#7a1f4a 55%,#b2142a 100%);padding:16px 17px}
.search-panel h2{color:var(--white);font-size:28px;font-weight:400;line-height:1.1;margin-bottom:14px;white-space:nowrap}
.field{height:40px;background:var(--white);margin-bottom:8px;display:flex;align-items:center;justify-content:space-between;padding:0 16px;font-size:13px;color:#555}
.search-btn{height:40px;background:#111;color:var(--white);text-align:center;line-height:40px;font-family:"Montserrat",sans-serif;font-weight:500;font-size:15px}

/* welcome */
.welcome-title{position:absolute;left:0;top:686px;width:1200px;text-align:center;color:var(--red);font-size:34px}
.welcome-text{position:absolute;left:143px;top:732px;width:914px;text-align:center;font-size:12.5px;line-height:22px;color:#333}
.video{position:absolute;left:360px;top:826px;width:480px;height:287px;background:linear-gradient(180deg,#6b6d70,#8f8f8e 50%,#b3b0a9)}
.play{position:absolute;left:214px;top:117px}

/* sections */
.band{position:absolute;left:0;width:1200px;background:var(--band)}
.section-title{position:absolute;left:143px;color:var(--red);font-size:33px}
.view-all{position:absolute;left:984px;width:72px;height:27px;line-height:27px;text-align:center;background:var(--navy);color:var(--white);font-family:"Montserrat",sans-serif;font-size:11px;border-radius:2px}
.card{position:absolute;width:219px;background:var(--white);box-shadow:0 1px 4px rgba(0,0,0,.15)}
.card-media{height:145px}
.card-body{padding:12px 10px 0}
.card-title{font-family:"Montserrat",sans-serif;font-size:13px;line-height:17px;color:var(--navy);font-weight:500}
.card-meta{font-size:9.5px;margin-top:10px;color:#111}
.card-desc{font-size:9.5px;line-height:16px;color:#555;margin-top:8px}

/* features */
.feature-title{position:absolute;left:0;top:2682px;width:1200px;text-align:center;color:var(--red);font-size:34px}
.feature{position:absolute;top:2746px;width:298px;height:192px;background:#efefef;text-align:center}
.feature svg{margin-top:30px}
.feature h3{font-size:20px;font-weight:400;margin-top:14px;color:#222}
.feature p{font-size:9.5px;line-height:14px;color:#555;padding:6px 20px 0}

/* newsletter */
.newsletter{position:absolute;left:0;top:3019px;width:1200px;height:191px;background:var(--navy-dark)}
.newsletter h2{position:absolute;left:0;top:40px;width:1200px;text-align:center;color:var(--white);font-size:33px;font-weight:400}
.email{position:absolute;left:400px;top:94px;width:400px;height:47px;background:var(--white);display:flex;align-items:center;justify-content:space-between;padding:0 18px 0 22px;font-family:"Montserrat",sans-serif;font-size:15px;color:#aaa}

/* footer */
.site-footer{position:absolute;left:0;top:3210px;width:1200px;height:122px;background:var(--footer);color:#bbb;font-size:11.5px}
.footer-links{position:absolute;left:143px;top:36px}
.footer-links span{margin:0 8px;color:#888}
.copyright{position:absolute;left:143px;top:65px}
.social{position:absolute;left:866px;top:50px;display:flex;gap:10px}
.social i{display:block;width:23px;height:23px;border-radius:50%;background:#5a6f9a}
</style>
</head>
<body>

<header class="site-header">
  <div class="brand"><span class="brand-dot"></span>Verdana Crest</div>
  <nav class="nav">
    <a class="active" style="left:491px">Courses</a>
    <a style="left:575px">Worksheets</a>
    <a style="left:680px">Quizzes</a>
    <a style="left:760px">Blog</a>
    <a style="left:818px">Support</a>
  </nav>
  <div class="btn btn-login">Login</div>
  <div class="btn btn-register">Register</div>
</header>

<section class="hero" role="img" aria-label="Man working on a laptop at a desk by a bright window">
  <svg class="hero-arrow" style="left:52px" width="20" height="30" viewBox="0 0 20 30"><path d="M17 2 4 15l13 13" fill="none" stroke="#1c3c7c" stroke-width="3"/></svg>
  <svg class="hero-arrow" style="left:1126px" width="20" height="30" viewBox="0 0 20 30"><path d="M3 2l13 13L3 28" fill="none" stroke="#1c3c7c" stroke-width="3"/></svg>
  <div class="search-panel">
    <h2>Aliquam erat volutpat</h2>
    <div class="field">Search Topic
      <svg width="16" height="13" viewBox="0 0 16 13"><g fill="#333"><rect x="0" y="0" width="3" height="3"/><rect x="4" y="0" width="12" height="3"/><rect x="0" y="5" width="3" height="3"/><rect x="4" y="5" width="12" height="3"/><rect x="0" y="10" width="3" height="3"/><rect x="4" y="10" width="12" height="3"/></g></svg>
    </div>
    <div class="field">Search Teacher
      <svg width="14" height="15" viewBox="0 0 14 15"><circle cx="7" cy="4" r="4" fill="#333"/><path d="M0 15c0-5 3-6 7-6s7 1 7 6z" fill="#333"/></svg>
    </div>
    <div class="search-btn">SEARCH</div>
  </div>
</section>

<h1 class="welcome-title">Welcome to Verdana Crest</h1>
<p class="welcome-text">Maecenas vel tortor accumsan quam varius imperdiet vel eget elit. Aenean facilisis tincidunt lectus, id dictum nisi luctus eget. Vivamus efficitur ex condimentum, malesuada eros eget, feugiat nibh. Sed tellus ex, imperdiet eget gravida sit amet, volutpat eget turpis. In nec ultricies est. Etiam mattis augue vehicula odio posuere, sit amet tempus lectus luctus. Nulla facilisi. Etiam vel massa elementum, bibendum tellus venenatis, feugiat massa.</p>
<div class="video" role="img" aria-label="Video cover: person relaxing in an armchair with a tablet">
  <svg class="play" width="52" height="52" viewBox="0 0 52 52"><circle cx="26" cy="26" r="23" fill="#fff" fill-opacity=".85" stroke="#fff" stroke-width="3"/><circle cx="26" cy="26" r="18" fill="#163a7a"/><path d="M21 17l14 9-14 9z" fill="#fff"/></svg>
</div>

<!-- Courses -->
<section class="band" style="top:1193px;height:496px"></section>
<h2 class="section-title" style="top:1264px">Courses</h2>
<div class="view-all" style="top:1271px">VIEW ALL</div>
<article class="card" style="left:143px;top:1321px;height:290px"><div class="card-media" role="img" aria-label="Student thinking at a table in a cafe" style="background:linear-gradient(135deg,#c8b9a5,#6f8fae)"></div><div class="card-body"><h3 class="card-title">Cras augue magna, placerat eget nulla congue suscipit</h3><p class="card-meta">By Ada Merrow</p><p class="card-desc">Etiam vel massa elementum, bibendum tellus venenatis, feugiat massa. Curabitur venenatis lacinia ornare.</p></div></article>
<article class="card" style="left:375px;top:1321px;height:290px"><div class="card-media" role="img" aria-label="Woman studying on a laptop" style="background:linear-gradient(135deg,#9a9691,#b89a6e)"></div><div class="card-body"><h3 class="card-title">Quisque aliquet ex nec est vestibulum pulvinar</h3><p class="card-meta">By Ada Merrow</p><p class="card-desc">Etiam vel massa elementum, bibendum tellus venenatis, feugiat massa. Curabitur venenatis lacinia ornare.</p></div></article>
<article class="card" style="left:607px;top:1321px;height:290px"><div class="card-media" role="img" aria-label="Man with headphones on a video call" style="background:linear-gradient(135deg,#8fa4b8,#3e5878)"></div><div class="card-body"><h3 class="card-title">Pellentesque convallis molestie enim sit amet efficitur</h3><p class="card-meta">By Ada Merrow</p><p class="card-desc">Etiam vel massa elementum, bibendum tellus venenatis, feugiat massa. Curabitur venenatis lacinia ornare.</p></div></article>
<article class="card" style="left:838px;top:1321px;height:290px"><div class="card-media" role="img" aria-label="Student watching an online lecture on a monitor" style="background:linear-gradient(135deg,#d6dbe0,#7a7d80)"></div><div class="card-body"><h3 class="card-title">Vivamus eleifend vitae nulla vel malesuada</h3><p class="card-meta">By Ada Merrow</p><p class="card-desc">Etiam vel massa elementum, bibendum tellus venenatis, feugiat massa. Curabitur venenatis lacinia ornare.</p></div></article>

<!-- Worksheets -->
<h2 class="section-title" style="top:1762px">Worksheets</h2>
<div class="view-all" style="top:1770px">VIEW ALL</div>
<article class="card" style="left:143px;top:1819px;height:210px"><div class="card-media" role="img" aria-label="Handwriting worksheet with flowers and bees" style="background:linear-gradient(180deg,#7fd0de 0%,#f07a8a 45%,#f6f6f6 60%)"></div><div class="card-body"><h3 class="card-title">Aenean sed quam non sapien faucibus consequat</h3></div></article>
<article class="card" style="left:375px;top:1819px;height:210px"><div class="card-media" role="img" aria-label="Counting worksheet with animal picture grid" style="background:linear-gradient(135deg,#f4f4f4,#cfe3c6)"></div><div class="card-body"><h3 class="card-title">Proin porta fermentum ipsum, vel porttitor turpis</h3></div></article>
<article class="card" style="left:607px;top:1819px;height:210px"><div class="card-media" role="img" aria-label="Colour-by-number worksheet of a race car" style="background:linear-gradient(180deg,#eeeeee 0%,#cccccc 78%,#e8c04a 86%)"></div><div class="card-body"><h3 class="card-title">Vivamus volutpat eu sapien quis tempus</h3></div></article>
<article class="card" style="left:838px;top:1819px;height:210px"><div class="card-media" role="img" aria-label="Addition puzzle worksheet on a beach scene" style="background:linear-gradient(135deg,#7cc6ea,#f0a24a)"></div><div class="card-body"><h3 class="card-title">Donec sit amet lectus nec mi tempor laoreet ac nec</h3></div></article>

<!-- Quizzes -->
<section class="band" style="top:2114px;height:495px"></section>
<h2 class="section-title" style="top:2183px">Quizzes</h2>
<div class="view-all" style="top:2192px">VIEW ALL</div>
<article class="card" style="left:143px;top:2242px;height:288px"><div class="card-media" role="img" aria-label="Printed crossword puzzle" style="background:linear-gradient(160deg,#2a2a2a,#d8dde3)"></div><div class="card-body"><h3 class="card-title">Mauris suscipit felis id nunc elementum varius</h3><p class="card-meta">Vivamus gravida sem a pretium</p><p class="card-desc">Etiam vel massa elementum, bibendum tellus venenatis, feugiat massa. Curabitur venenatis lacinia ornare.</p></div></article>
<article class="card" style="left:375px;top:2242px;height:288px"><div class="card-media" role="img" aria-label="Maze puzzle activity sheet" style="background:linear-gradient(135deg,#e4e4e4,#f7f7f7)"></div><div class="card-body"><h3 class="card-title">Nullam accumsan purus vel tempus viverra</h3><p class="card-meta">Nam lobortis purus fringilla</p><p class="card-desc">Etiam vel massa elementum, bibendum tellus venenatis, feugiat massa. Curabitur venenatis lacinia ornare.</p></div></article>
<article class="card" style="left:607px;top:2242px;height:288px"><div class="card-media" role="img" aria-label="Matching quiz with coloured umbrellas" style="background:linear-gradient(135deg,#f2f2f2,#8a9ed0)"></div><div class="card-body"><h3 class="card-title">Praesent elementum nulla sit amet justo</h3><p class="card-meta">Vestibulum facilisis dolor at purus</p><p class="card-desc">Etiam vel massa elementum, bibendum tellus venenatis, feugiat massa. Curabitur venenatis lacinia ornare.</p></div></article>
<article class="card" style="left:838px;top:2242px;height:288px"><div class="card-media" role="img" aria-label="Garden maze game with palm trees" style="background:linear-gradient(180deg,#a8dcf0 0%,#8cc63f 40%,#d9b25a 100%)"></div><div class="card-body"><h3 class="card-title">Nam et tortor in ante iaculis porttitor in luctus</h3><p class="card-meta">Phasellus blandit quam</p><p class="card-desc">Etiam vel massa elementum, bibendum tellus venenatis, feugiat massa. Curabitur venenatis lacinia ornare.</p></div></article>

<!-- Features -->
<h2 class="feature-title">Nunc pretium commodo arcu</h2>
<div class="feature" style="left:143px">
  <svg width="54" height="58" viewBox="0 0 54 58" fill="none" stroke="#1c3c7c" stroke-width="2"><path d="M27 2 4 12l23 10 23-10z"/><path d="M14 17v9c0 5 26 5 26 0v-9"/><path d="M48 13v12"/><path d="M6 56c0-12 9-18 21-18s21 6 21 18z"/><path d="M22 40l5 8 5-8"/></svg>
  <h3>Duis rutrum venenatis</h3>
  <p>Etiam vel massa elementum, bibendum tellus venenatis, feugiat massa. Curabitur venenatis lacinia.</p>
</div>
<div class="feature" style="left:451px">
  <svg width="58" height="58" viewBox="0 0 58 58" fill="none" stroke="#1c3c7c" stroke-width="2"><rect x="4" y="4" width="28" height="18" rx="2"/><path d="M10 22v7l7-7"/><rect x="26" y="14" width="28" height="18" rx="2"/><path d="M46 32v7l-7-7"/><circle cx="16" cy="38" r="6"/><path d="M4 56c0-7 5-10 12-10s12 3 12 10"/><circle cx="42" cy="44" r="5"/><path d="M32 56c0-5 4-7 10-7s10 2 10 7"/></svg>
  <h3>Vestibulum ultrices</h3>
  <p>Etiam vel massa elementum, bibendum tellus venenatis, feugiat massa. Curabitur venenatis lacinia.</p>
</div>
<div class="feature" style="left:758px">
  <svg width="60" height="56" viewBox="0 0 60 56" fill="none" stroke="#1c3c7c" stroke-width="2"><rect x="2" y="4" width="56" height="38" rx="2"/><rect x="7" y="9" width="46" height="28"/><path d="M24 42l-3 10h18l-3-10M16 53h28"/><circle cx="18" cy="20" r="4"/><path d="M11 33c0-5 3-7 7-7s7 2 7 7"/><rect x="30" y="14" width="18" height="10"/><path d="M30 29h18"/></svg>
  <h3>Suspendisse potenti</h3>
  <p>Etiam vel massa elementum, bibendum tellus venenatis, feugiat massa. Curabitur venenatis lacinia.</p>
</div>

<!-- Newsletter -->
<section class="newsletter">
  <h2>Newsletter Sign Up</h2>
  <div class="email">Email Address
    <svg width="20" height="15" viewBox="0 0 20 15"><rect width="20" height="15" rx="1" fill="#6a5bb3"/><path d="M1 1l9 7 9-7" fill="none" stroke="#fff" stroke-width="1.5"/></svg>
  </div>
</section>

<footer class="site-footer">
  <div class="footer-links">Home<span>|</span>Courses<span>|</span>Worksheets<span>|</span>Quizzes<span>|</span>Blog<span>|</span>Support</div>
  <div class="copyright">Copyright © 2019 Verdana Crest. All rights reserved.</div>
  <div class="social" aria-label="Social links"><i></i><i></i><i></i><i></i><i></i><i></i></div>
</footer>

</body>
</html>
```